Process Serving Company needs a letterhead design

Looking to have a letterhead designed for letters to attorneys advertising our business. We would like something eye catching but professional. Colors and logos are attached. Please add "Process Service and Attorney Support" near the logo or header

Target Market(s)

Attorneys

Font styles to use
Serif
Sans Serif

Colors
33a6d7
0255a3
85cae6
cee9f5
ecf7fb

```html
<!DOCTYPE html>
<html lang="en">
<head>
<meta charset="utf-8">
<title>Canyon Swift Serve Letterhead</title>
<link rel="stylesheet" href="https://fonts.googleapis.com/css2?family=Open+Sans:wght@400;600&family=Roboto:wght@400&display=swap">
<style>
  :root {
    --brand-blue: #33a6d7;
    --deep-blue: #0255a3;
    --soft-blue: #85cae6;
    --pale-blue: #cee9f5;
    --mist-blue: #ecf7fb;
    --ink: #3a3a3a;
    --muted-grey: #8a8c8f;
    --paper: #ffffff;
  }
  * { margin: 0; padding: 0; box-sizing: border-box; }
  html, body { width: 1063px; height: 1200px; overflow: hidden; }
  body { background: var(--paper); font-family: "Open Sans", sans-serif; color: var(--ink); }

  .letterhead {
    position: relative;
    width: 1063px;
    height: 1200px;
    background: linear-gradient(180deg, #ffffff 0%, #ffffff 55%, #f6f6f7 100%);
    overflow: hidden;
  }

  .brand {
    position: absolute;
    left: 110px;
    top: 108px;
  }
  .brand-line {
    display: flex;
    align-items: center;
    gap: 14px;
  }
  .brand-mark {
    width: 22px;
    height: 22px;
    background: var(--brand-blue);
  }
  .brand-name {
    font-weight: 600;
    font-size: 30px;
    letter-spacing: 1px;
    color: var(--brand-blue);
    text-transform: uppercase;
  }
  .brand-tagline {
    margin-top: 6px;
    padding-left: 36px;
    font-size: 13px;
    letter-spacing: 0.6px;
    color: var(--deep-blue);
  }

  .contact {
    position: absolute;
    left: 700px;
    top: 78px;
    font-family: "Roboto", sans-serif;
    font-style: normal;
    font-size: 15px;
    line-height: 19px;
    color: var(--ink);
  }
  .contact-address { margin-bottom: 4px; }
  .contact-list { list-style: none; }
  .contact-list li { display: flex; align-items: center; gap: 8px; padding-left: 12px; }
  .contact-list svg { width: 12px; height: 12px; fill: var(--brand-blue); flex: none; }

  .watermark-area {
    position: absolute;
    right: 40px;
    top: 600px;
    width: 300px;
    height: 300px;
    background: linear-gradient(135deg, var(--mist-blue), rgba(236,247,251,0.2));
    opacity: 0.8;
  }

  .letter-body {
    position: absolute;
    left: 190px;
    top: 290px;
    width: 770px;
    font-size: 15px;
    line-height: 21px;
    letter-spacing: 0.3px;
  }
  .salutation { margin-bottom: 22px; }
  .paragraph { margin-bottom: 20px; padding-left: 14px; }
  .closing { margin-top: 28px; padding-left: 24px; }

  .signature-area {
    margin: 14px 0 0 40px;
    width: 130px;
    height: 80px;
    background: linear-gradient(135deg, #f1f1f2, #e2e3e5);
    border-radius: 4px;
  }

  .memberships {
    position: absolute;
    left: 270px;
    bottom: 60px;
    display: flex;
    gap: 34px;
    align-items: center;
  }
  .membership-badge {
    width: 96px;
    height: 52px;
    background: var(--muted-grey);
    opacity: 0.55;
    border-radius: 6px;
  }
</style>
</head>
<body>
  <main class="letterhead">
    <header>
      <div class="brand">
        <div class="brand-line">
          <span class="brand-mark"></span>
          <span class="brand-name">Canyon Swift Serve</span>
        </div>
        <p class="brand-tagline">Process Service and Attorney Support</p>
      </div>

      <address class="contact">
        <div class="contact-address">4521 E Mesquite Rd STE 210<br>Tempe AZ 85281</div>
        <ul class="contact-list">
          <li>
            <svg viewBox="0 0 24 24" aria-hidden="true"><path d="M6.6 10.8a15.5 15.5 0 0 0 6.6 6.6l2.2-2.2c.3-.3.7-.4 1-.2 1.1.4 2.3.6 3.6.6.6 0 1 .4 1 1V20c0 .6-.4 1-1 1A17 17 0 0 1 3 4c0-.6.4-1 1-1h3.5c.6 0 1 .4 1 1 0 1.3.2 2.5.6 3.6.1.3 0 .7-.2 1z"/></svg>
            555-201-4400
          </li>
          <li>
            <svg viewBox="0 0 24 24" aria-hidden="true"><path d="M6 2h12v5H6zM4 8h16a2 2 0 0 1 2 2v7h-4v5H6v-5H2v-7a2 2 0 0 1 2-2zm4 8v4h8v-4z"/></svg>
            555-201-4411
          </li>
          <li>
            <svg viewBox="0 0 24 24" aria-hidden="true"><path d="M2 5h20v14H2zm2 2v.5l8 5 8-5V7z"/></svg>
            jordan@CanyonSwift.com
          </li>
          <li>
            <svg viewBox="0 0 24 24" aria-hidden="true"><circle cx="12" cy="12" r="10"/></svg>
            www.CanyonSwift.com
          </li>
        </ul>
      </address>
    </header>

    <div class="watermark-area" role="img" aria-label="Faint decorative document watermark area"></div>

    <section class="letter-body">
      <p class="salutation">Dear customer,</p>
      <p class="paragraph">Lorem ipsum dolor sit amet, consectetur adipisicing elit, sed do eiusmod tempor incididunt ut labore et dolore magna aliqua. Ut enim ad minim veniam, quis nostrud exercitation ullamco laboris nisi ut aliquip ex ea commodo consequat. Duis aute irure dolor in reprehenderit in voluptate velit esse cillum dolore eu fugiat nulla pariatur. Excepteur sint occaecat cupidatat non proident, sunt in culpa qui officia deserunt mollit anim id est laborum.</p>
      <p class="paragraph">Lorem ipsum dolor sit amet, consectetur adipisicing elit, sed do eiusmod tempor incididunt ut labore et dolore magna aliqua. Ut enim ad minim veniam, quis nostrud exercitation ullamco laboris nisi ut aliquip ex ea commodo consequat. Duis aute irure dolor in reprehenderit in voluptate velit esse cillum dolore eu fugiat nulla pariatur. Excepteur sint occaecat cupidatat non proident, sunt in culpa qui officia deserunt mollit anim id est laborum.</p>
      <p class="paragraph">Lorem ipsum dolor sit amet, consectetur adipisicing elit, sed do eiusmod tempor incididunt ut labore et dolore magna aliqua. Ut enim ad minim veniam, quis nostrud exercitation ullamco laboris nisi ut aliquip ex ea commodo consequat. Duis aute irure dolor in reprehenderit in voluptate velit esse cillum dolore eu fugiat nulla pariatur. Excepteur sint occaecat cupidatat non proident, sunt in culpa qui officia deserunt mollit anim id est laborum.</p>
      <p class="paragraph">Lorem ipsum dolor sit amet, consectetur adipisicing elit, sed do eiusmod tempor incididunt ut labore et dolore magna aliqua. Ut enim ad minim veniam, quis nostrud exercitation ullamco laboris nisi ut aliquip ex ea commodo consequat. Duis aute irure dolor in reprehenderit.</p>
      <p class="closing">Yours Sincerely,</p>
      <div class="signature-area" role="img" aria-label="Handwritten signature"></div>
    </section>

    <footer class="memberships">
      <div class="membership-badge" role="img" aria-label="Professional association membership badge"></div>
      <div class="membership-badge" role="img" aria-label="State association membership badge"></div>
    </footer>
  </main>
</body>
</html>
```